New Baby product needs fun and creative design

We are about to launch are new product for babies and we need some amazing packaging, the product is a snot sucker for blocked noses also known as a nasal aspirator, We are looking for a Creative with a Capital C packaging, we want a nice concept on the box an illustration of a baby and mum using the product like pic attached (example 1) or maybe an illustration of a baby with the pipe, the design has to be new and up to date, I am looking for an animated type feel. Something that make it look baby friendly and comfortable

The packaging is a rectangular box

The colours should be matched with the logo(Baby PIXU) but if not it is still fine as long as there is not a big contrast

Full text for the box will be provided for back and front, the main design will be for the front of the box

Target Market(s)

Mum's with new born babies

Industry/Entity Type

Baby

Requirements
Must have
• Illustration of showing a mum and baby like the example 1
Nice to have
• An animated illustration of a mother and baby using the product or a baby with the pipe in it's nose, something that would look friendly and welcoming for mums
Should not have
• solid colours and medicine like aligned instructional text on the front. Old style designs, should be in line with current designs similar to picture shown

```html
<!DOCTYPE html>
<html lang="en">
<head>
<meta charset="utf-8">
<title>Baby PIXU Nasal Aspirator – Packaging</title>
<link rel="stylesheet" href="https://fonts.googleapis.com/css2?family=Luckiest+Guy&family=Open+Sans:ital,wght@0,400;0,600;0,700;1,400&display=swap">
<style>
  :root {
    --bg: #b9c6d6;
    --paper: #ffffff;
    --rose: #c9669b;
    --rose-light: #e9a9cb;
    --rose-deep: #9b4a78;
    --lime: #8cc21a;
    --lime-light: #c3e35a;
    --lime-deep: #5f9410;
    --ink: #3b3b3b;
    --side-blue: #2a86c8;
    --side-red: #d9386a;
  }
  * { box-sizing: border-box; margin: 0; padding: 0; }
  html, body { width: 1200px; height: 1200px; overflow: hidden; }
  body {
    background: var(--bg);
    font-family: "Open Sans", Arial, sans-serif;
    display: flex;
    align-items: center;
    justify-content: center;
  }
  .canvas {
    width: 1200px;
    height: 1200px;
    display: flex;
    align-items: center;
    justify-content: center;
    gap: 40px;
  }
  .box-net { display: flex; box-shadow: 0 10px 30px rgba(40,60,90,.25); }
  .panel { width: 420px; height: 575px; display: block; }
  .panel--side { width: 220px; }
  .brand-name {
    font-family: "Open Sans", Arial, sans-serif;
    font-weight: 600;
  }
  .product-title {
    font-family: "Luckiest Guy", "Arial Black", Impact, sans-serif;
    font-weight: 400;
  }
  .tagline {
    font-family: "Open Sans", Arial, sans-serif;
    font-size: 16px;
    letter-spacing: .5px;
  }
  .side-heading { font-weight: 700; font-size: 12px; }
  .side-copy { font-size: 11px; fill: var(--ink); }
</style>
</head>
<body>
<main class="canvas">

  <!-- Rose edition: side panel + front -->
  <div class="box-net box-net--rose">
    <svg class="panel panel--side" viewBox="0 0 220 575" xmlns="http://www.w3.org/2000/svg">
      <defs>
        <linearGradient id="side-rose" x1="0" y1="0" x2="0" y2="1">
          <stop offset="0" stop-color="#e4a0c4"/>
          <stop offset="1" stop-color="#a94f82"/>
        </linearGradient>
      </defs>
      <rect width="220" height="575" fill="#f2f2f4"/>
      <polygon points="0,300 220,250 220,575 0,575" fill="url(#side-rose)"/>
      <circle cx="30" cy="46" r="7" fill="var(--rose)"/>
      <text class="brand-name" x="44" y="51" font-size="15" fill="var(--rose)">Baby PIXU</text>

      <text class="side-heading" x="20" y="112" fill="var(--side-blue)">This box Contains:</text>
      <g class="side-copy">
        <circle cx="24" cy="128" r="2.5" fill="var(--side-red)"/><text x="32" y="132">Suction Pipe</text>
        <circle cx="24" cy="146" r="2.5" fill="var(--side-red)"/><text x="32" y="150">Replaceable Heads</text>
        <circle cx="24" cy="164" r="2.5" fill="var(--side-red)"/><text x="32" y="168">Sanitary Box</text>
      </g>

      <text class="side-heading" x="20" y="222" fill="var(--side-blue)">Directions for Use:</text>
      <text class="side-copy">
        <tspan x="20" y="242">Gently position the end</tspan>
        <tspan x="20" y="258">of the tubing into the edge</tspan>
        <tspan x="20" y="274">of baby's nostril. Using</tspan>
        <tspan x="20" y="290">the mouth piece attached,</tspan>
        <tspan x="20" y="306">gently suction mucus out</tspan>
        <tspan x="20" y="322">of baby's nostril and into</tspan>
        <tspan x="20" y="338">the nozzle.</tspan>
        <tspan x="20" y="362">After Use: Rinse aspirator</tspan>
        <tspan x="20" y="378">with warm soapy water</tspan>
        <tspan x="20" y="394">and return to sanitary box</tspan>
        <tspan x="20" y="410">ready for the next use.</tspan>
      </text>

      <text class="side-heading" x="20" y="448" fill="var(--side-blue)">Please note:</text>
      <text class="side-copy">
        <tspan x="20" y="468">Once opened, remove</tspan>
        <tspan x="20" y="484">tubing and pipe with care</tspan>
        <tspan x="20" y="500">from the sanitary box.</tspan>
      </text>
    </svg>

    <svg class="panel panel--front" viewBox="0 0 420 575" xmlns="http://www.w3.org/2000/svg">
      <defs>
        <linearGradient id="band-rose" x1="0" y1="0" x2="1" y2="1">
          <stop offset="0" stop-color="#e7a3c7"/>
          <stop offset="1" stop-color="#a64e80"/>
        </linearGradient>
        <radialGradient id="art-rose" cx="0.5" cy="0.45" r="0.6">
          <stop offset="0" stop-color="#ffffff" stop-opacity=".85"/>
          <stop offset="1" stop-color="#f3d6e5" stop-opacity=".55"/>
        </radialGradient>
      </defs>
      <rect width="420" height="575" fill="var(--paper)"/>
      <polygon points="0,265 210,360 420,225 420,575 0,575" fill="url(#band-rose)"/>
      <polygon points="210,360 420,225 420,575" fill="#ffffff" opacity=".12"/>
      <polygon points="0,265 210,360 0,575" fill="#ffffff" opacity=".18"/>

      <ellipse cx="255" cy="375" rx="160" ry="190" fill="url(#art-rose)"
               role="img" aria-label="Line illustration of a mother in profile holding her newborn baby close"/>

      <circle cx="150" cy="62" r="8" fill="var(--rose)"/>
      <text class="brand-name" x="166" y="69" font-size="22" fill="var(--rose)">Baby PIXU</text>

      <text class="product-title" x="210" y="150" text-anchor="middle" font-size="48"
            textLength="370" lengthAdjust="spacingAndGlyphs" fill="var(--rose)">Nasal Aspirator</text>

      <path id="tag-path-rose" d="M34,318 Q58,560 400,546" fill="none"/>
      <text class="tagline" fill="#ffffff"><textPath href="#tag-path-rose">Gently clear baby's blocked nose in seconds</textPath></text>
    </svg>
  </div>

  <!-- Lime edition: front -->
  <div class="box-net box-net--lime">
    <svg class="panel panel--front" viewBox="0 0 420 575" xmlns="http://www.w3.org/2000/svg">
      <defs>
        <linearGradient id="band-lime" x1="0" y1="0" x2="1" y2="1">
          <stop offset="0" stop-color="#c6e55c"/>
          <stop offset="1" stop-color="#6fa512"/>
        </linearGradient>
        <radialGradient id="art-lime" cx="0.5" cy="0.45" r="0.6">
          <stop offset="0" stop-color="#ffffff" stop-opacity=".85"/>
          <stop offset="1" stop-color="#e3f2bf" stop-opacity=".55"/>
        </radialGradient>
      </defs>
      <rect width="420" height="575" fill="var(--paper)"/>
      <polygon points="0,265 210,360 420,225 420,575 0,575" fill="url(#band-lime)"/>
      <polygon points="210,360 420,225 420,575" fill="#ffffff" opacity=".12"/>
      <polygon points="0,265 210,360 0,575" fill="#ffffff" opacity=".18"/>

      <ellipse cx="255" cy="375" rx="160" ry="190" fill="url(#art-lime)"
               role="img" aria-label="Line illustration of a mother in profile holding her newborn baby close"/>

      <circle cx="150" cy="62" r="8" fill="var(--lime)"/>
      <text class="brand-name" x="166" y="69" font-size="22" fill="var(--lime)">Baby PIXU</text>

      <text class="product-title" x="210" y="150" text-anchor="middle" font-size="48"
            textLength="370" lengthAdjust="spacingAndGlyphs" fill="var(--lime)">Nasal Aspirator</text>

      <path id="tag-path-lime" d="M34,318 Q58,560 400,546" fill="none"/>
      <text class="tagline" fill="#ffffff"><textPath href="#tag-path-lime">Gently clear baby's blocked nose in seconds</textPath></text>
    </svg>
  </div>

</main>
</body>
</html>
```